Bramblecrest fieldworks outfitters

I want a full wrap other than the top of the van.
My services include hvac central A/C, heat pumps,
Fresh air systems, as well as beer and soda systems, air compressors and cryogenics. I have a 2013 Korvath TX 4100 van high roof

Target Market(s)

Residential and commercial

Industry/Entity Type

HVAC , air compressors, beer and soda systems

Requirements
Nice to have
• Image or design that stands out. Looks sleek and original

```html
<!DOCTYPE html>
<html lang="en">
<head>
<meta charset="utf-8">
<title>Bramblecrest Fieldworks Outfitters – Van Wrap Side Panel</title>
<link href="https://fonts.googleapis.com/css2?family=Montserrat:wght@600;700;800&display=swap" rel="stylesheet">
<style>
  :root {
    --wrap-red: #d8140f;
    --wrap-white: #f6f6f2;
    --accent-blue: #3a6fe0;
    --brand-navy: #0d1f8c;
    --ink-black: #141414;
    --phone-red: #d01212;
    --backdrop: #e4e7e8;
  }
  html, body {
    margin: 0;
    padding: 0;
    width: 1200px;
    height: 1000px;
    overflow: hidden;
    background: var(--backdrop);
  }
  .wrap-canvas {
    display: block;
    width: 1200px;
    height: 1000px;
  }
  .panel-red { fill: var(--wrap-red); }
  .panel-white { fill: var(--wrap-white); }
  .swoosh-line { fill: none; stroke: var(--accent-blue); stroke-width: 7; stroke-linecap: round; }
  .brand-dot { fill: var(--brand-navy); }
  .brand-name {
    font-family: "Montserrat", sans-serif;
    font-weight: 800;
    fill: var(--brand-navy);
  }
  .tagline {
    font-family: "Montserrat", sans-serif;
    font-weight: 800;
    fill: var(--ink-black);
    letter-spacing: 0.5px;
  }
  .service-list {
    font-family: "Montserrat", sans-serif;
    font-weight: 700;
    font-size: 16px;
    fill: var(--brand-navy);
  }
  .phone-number {
    font-family: "Montserrat", sans-serif;
    font-weight: 800;
    font-size: 29px;
    fill: var(--phone-red);
  }
</style>
</head>
<body>
<svg class="wrap-canvas" viewBox="0 0 1200 1000" xmlns="http://www.w3.org/2000/svg">
  <g class="side-panel">
    <rect class="panel-red" x="30" y="270" width="1140" height="460" rx="10"/>
    <path class="panel-white" d="M168,270 C118,330 128,440 250,505 C420,600 650,682 870,690 L1170,690 L1170,270 Z"/>
    <rect class="panel-white" x="870" y="689" width="300" height="41"/>
    <path class="swoosh-line" d="M172,305 C158,400 228,470 330,522 C500,610 700,684 908,684"/>
  </g>

  <g class="main-brand">
    <circle class="brand-dot" cx="226" cy="378" r="40"/>
    <text class="brand-name" x="622" y="362" text-anchor="end" font-size="36">BRAMBLECREST</text>
    <text class="brand-name" x="622" y="388" text-anchor="end" font-size="21">Fieldworks Outfitters</text>
    <text class="tagline" x="622" y="410" text-anchor="end" font-size="17">SERVICE AHEAD OF SCHEDULE</text>
  </g>

  <g class="service-list" text-anchor="end">
    <text x="596" y="450">• Restaurants &amp; Bar Equipment</text>
    <text x="596" y="473">• Beer &amp; Soda Systems</text>
    <text x="596" y="497">• Air Compressor/Dryers</text>
    <text x="596" y="520">• IAQ Testing &amp; Monitoring</text>
    <text x="596" y="543">• Piping &amp; Heat Pumps</text>
    <text x="596" y="567">• HVAC Services</text>
    <text x="596" y="590">• Cryogenics</text>
  </g>

  <g class="door-brand" text-anchor="end">
    <text class="brand-name" x="855" y="580" font-size="22">BRAMBLECREST</text>
    <text class="brand-name" x="855" y="598" font-size="14">Fieldworks Outfitters</text>
    <text class="tagline" x="855" y="613" font-size="10.5">SERVICE AHEAD OF SCHEDULE</text>
    <text class="phone-number" x="855" y="643">555-014-2297</text>
  </g>
</svg>
</body>
</html>
```